Coral Bay Pools New website

I currently operate a swimming pool service and repair business and looking for a re design for my website as it has been over 5 years since it was designed. current site is coralbaypoolslv.com

```html
<!DOCTYPE html>
<html lang="en">
<head>
<meta charset="utf-8">
<title>Coral Bay Pools</title>
<link rel="stylesheet" href="https://fonts.googleapis.com/css2?family=Outfit:wght@500;600;700&family=Montserrat:wght@400;500;600&display=swap">
<style>
:root{
  --navy:#1c4584;
  --blue-dark:#0b5b9a;
  --blue:#3b9ad8;
  --blue-deep:#1b5fa8;
  --orange:#f9a11b;
  --ink:#222;
  --text:#3a3a3a;
  --paper:#f4f4f2;
  --footer:#1e2633;
  --white:#fff;
}
*{margin:0;padding:0;box-sizing:border-box}
html,body{width:1200px;height:4057px;overflow:hidden;background:var(--white)}
body{position:relative;font-family:"Montserrat",sans-serif;color:var(--text)}
.abs{position:absolute}
.heading{font-family:"Outfit",sans-serif;font-weight:600;color:var(--ink)}
.btn{position:absolute;background:var(--orange);color:var(--white);border-radius:16px;font-family:"Montserrat",sans-serif;font-weight:600;font-size:11px;text-transform:uppercase;display:flex;align-items:center;justify-content:center;letter-spacing:.3px}
.photo{position:absolute}
.brand{position:absolute;display:flex;align-items:center;gap:10px;font-family:"Outfit",sans-serif;font-weight:700;color:var(--navy);font-size:26px;white-space:nowrap}
.brand .dot{width:22px;height:22px;border-radius:50%;background:var(--orange)}

/* header */
.palm-left{left:0;top:0;width:165px;height:245px;background:radial-gradient(circle at 10% 40%,#6f9a3e 0,#9fbf5a 35%,rgba(255,255,255,0) 70%)}
.palm-right{right:0;top:0;width:140px;height:210px;background:radial-gradient(circle at 90% 30%,#6f9a3e 0,#a4c35f 35%,rgba(255,255,255,0) 70%)}
.nav-rule{left:161px;top:190px;width:878px;height:1px;background:#e4e4e4}
.nav a{position:absolute;top:211px;font-size:13px;color:#444;text-decoration:none}
.nav a.active{color:#1d6fb8;font-weight:600}
.nav .caret{display:inline-block;width:6px;height:6px;border-right:1.5px solid #444;border-bottom:1.5px solid #444;transform:rotate(45deg);margin-left:6px;position:relative;top:-3px}

/* hero */
.hero-photo{left:0;top:244px;width:1200px;height:720px;background:linear-gradient(180deg,#8a8a86 0%,#a9a7a1 30%,#4fa9d6 55%,#2f8fce 75%,#d9cdb5 100%)}
.hero-card{left:551px;top:365px;width:580px;height:249px;background:rgba(255,255,255,.92);border-radius:26px}
.hero-title{left:599px;top:398px;width:520px;font-family:"Outfit",sans-serif;font-weight:600;font-size:41px;line-height:45px;color:var(--navy)}
.hero-sub{left:599px;top:503px;font-size:13px;color:#333}
.arrow{position:absolute;top:472px;width:36px;height:36px;border-radius:50%;background:rgba(255,255,255,.85);display:flex;align-items:center;justify-content:center}

/* about */
.about-title{left:0;width:1200px;top:1055px;text-align:center;font-size:34px}
.about-text{left:233px;width:734px;top:1106px;text-align:center;font-size:12.6px;line-height:16.4px;color:#333}
.about-photo{left:905px;top:1085px;width:295px;height:280px;border-radius:120px 0 0 0;background:linear-gradient(135deg,#f1e0c8 0%,#e08a3c 45%,#9ac8d8 100%)}

/* why */
.why-left{left:0;top:1368px;width:600px;height:480px;background:var(--blue-dark)}
.why-photo{left:600px;top:1340px;width:600px;height:535px;background:linear-gradient(180deg,#b9cde0 0%,#6f6a55 35%,#7a8a4c 55%,#3fa6d8 80%,#2a86c4 100%)}
.why-title{left:85px;top:1495px;font-size:34px;color:var(--white)}
.why-text{left:85px;top:1551px;width:400px;font-size:12.6px;line-height:17.5px;color:var(--white)}

/* services */
.services-bg{left:0;top:1843px;width:1200px;height:700px;background:var(--blue)}
.services-title{left:0;width:1200px;top:1930px;text-align:center;font-size:34px;color:var(--white)}
.card-photo{position:absolute;top:2022px;width:351px;height:281px;border-radius:14px;border:4px solid rgba(255,255,255,.55)}
.card-title{position:absolute;top:2324px;width:351px;text-align:center;font-family:"Outfit",sans-serif;font-weight:600;font-size:19px;color:var(--white)}
.card-text{position:absolute;top:2361px;width:351px;text-align:center;font-size:12.5px;line-height:16px;color:var(--white);padding:0 22px}

/* contact */
.contact-bg{left:0;top:2560px;width:1200px;height:640px;background:var(--paper)}
.contact-title{left:0;width:1200px;top:2680px;text-align:center;font-size:34px}
.field{position:absolute;background:var(--white);border:1px solid #cfcfcf;border-radius:26px;font-size:11.5px;color:#555;padding:17px 26px}
.contact-photo{left:0;top:2788px;width:307px;height:378px;background:radial-gradient(ellipse at 35% 45%,#f2c18a 0,#e9a257 35%,#5fb6e0 75%,rgba(244,244,242,0) 100%)}

/* cta */
.cta-photo{left:0;top:3158px;width:1200px;height:540px;background:linear-gradient(180deg,#46523f 0%,#6b6e60 40%,#4d6f86 70%,#2f5675 100%)}
.cta-box{left:348px;top:3303px;width:504px;height:244px;background:rgba(20,95,170,.82);border-radius:6px}
.cta-title{left:348px;width:504px;top:3345px;text-align:center;font-family:"Outfit",sans-serif;font-weight:600;font-size:50px;line-height:62px;color:var(--white)}

/* footer */
.footer-bg{left:0;top:3690px;width:1200px;height:367px;background:var(--footer)}
.footer-nav a{position:absolute;top:3879px;font-size:13px;color:var(--white);text-decoration:none}
.footer-rule{left:161px;width:878px;height:1px;background:#3a4454}
.contact-item{position:absolute;top:3950px;display:flex;align-items:center;gap:10px;color:var(--white);font-size:12.5px}
.contact-icon{width:26px;height:26px;border-radius:50%;background:var(--orange);display:flex;align-items:center;justify-content:center}
.social{position:absolute;top:3955px;width:16px;height:16px;border-radius:50%;border:2px solid var(--white)}
.copyright{left:0;width:1200px;top:4020px;text-align:center;font-size:12.5px;color:var(--white)}
</style>
</head>
<body>

<!-- header -->
<div class="photo abs palm-left" role="img" aria-label="Palm fronds"></div>
<div class="photo abs palm-right" role="img" aria-label="Palm fronds"></div>
<div class="brand" style="left:493px;top:78px"><span class="dot"></span>Coral Bay Pools</div>
<div class="abs nav-rule"></div>
<nav class="nav">
  <a class="active" style="left:316px">Home</a>
  <a style="left:417px">About Us</a>
  <a style="left:535px">Our Services<span class="caret"></span></a>
  <a style="left:679px">Free Estimate</a>
  <a style="left:830px">Contact</a>
</nav>

<!-- hero -->
<div class="photo hero-photo" role="img" aria-label="Two friends relaxing with drinks on the edge of a blue pool"></div>
<svg class="abs" style="left:0;top:640px" width="1200" height="330" viewBox="0 0 1200 330">
  <path d="M0,55 C280,40 430,250 680,200 C880,160 1040,55 1200,20 L1200,330 L0,330Z" fill="#3b9ad8"/>
  <path d="M0,135 C290,150 440,300 650,300 C880,300 1040,150 1200,115 L1200,330 L0,330Z" fill="#1b5fa8"/>
  <path d="M0,147 C290,162 440,312 650,312 C880,312 1040,163 1200,128 L1200,330 L0,330Z" fill="#d9cdb5"/>
  <path d="M0,190 C300,220 450,340 650,330 L0,330Z" fill="#fff"/>
  <path d="M650,330 C860,320 1040,220 1200,205 L1200,330Z" fill="#fff"/>
</svg>
<div class="abs hero-card"></div>
<h1 class="abs hero-title">Welcome Nevada’s Top Reviewed Pool Cleaning</h1>
<p class="abs hero-sub">When you need professional pool cleaning services in Nevada.</p>
<div class="btn" style="left:601px;top:541px;width:140px;height:32px">Free Estimate</div>
<div class="arrow" style="left:15px"><svg width="14" height="14" viewBox="0 0 14 14"><path d="M9 2 L4 7 L9 12" stroke="#333" stroke-width="1.6" fill="none"/></svg></div>
<div class="arrow" style="left:1147px"><svg width="14" height="14" viewBox="0 0 14 14"><path d="M5 2 L10 7 L5 12" stroke="#333" stroke-width="1.6" fill="none"/></svg></div>

<!-- about -->
<div class="photo abs about-photo" role="img" aria-label="Woman in sunhat and sunglasses lounging poolside"></div>
<h2 class="abs heading about-title">Welcome About Us</h2>
<p class="abs about-text">When you need professional pool cleaning services in Nevada, you can count on the professionals at Coral Bay Pools to provide you with superior and prompt solutions. Whether you need assistance with a residential or commercial pool, we’ll vacuum, brush, and thoroughly clean your pool so it’s swim-ready. We’ll also clean your pool filters and inform you of any issues that arise. Our staff is certified by the Desert Valley Health Board to ensure proper chemical levels and equipment are safe. To learn more about our pool cleaning services or to get your free estimate, contact our pool experts today.</p>
<div class="btn" style="left:541px;top:1225px;width:118px;height:32px">Learn More</div>

<!-- why choose us -->
<div class="photo why-photo" role="img" aria-label="Man jumping into a backyard pool with a splash"></div>
<div class="abs why-left"></div>
<svg class="abs" style="left:0;top:1330px" width="600" height="60" viewBox="0 0 600 60">
  <path d="M0,38 C150,20 300,20 600,40 L600,60 L0,60Z" fill="#0b5b9a"/>
  <path d="M80,30 C200,8 380,10 560,35 C380,22 200,22 80,30Z" fill="#3b9ad8"/>
</svg>
<h2 class="abs heading why-title">Why Choose Us?</h2>
<p class="abs why-text">Our full-service pool company proudly serves the entire Las Vegas valley, and we’re certified by the Desert Valley Health Board to maintain the highest level of pool safety. If you need repairs, maintenance, scheduled cleanings, or any other pool services, contact us online or by phone today.</p>
<div class="btn" style="left:85px;top:1679px;width:132px;height:32px">Contact Us</div>

<!-- services -->
<div class="abs services-bg"></div>
<svg class="abs" style="left:0;top:1820px" width="1200" height="60" viewBox="0 0 1200 60">
  <path d="M0,30 C250,0 420,5 600,25 L600,60 L0,60Z" fill="#3b9ad8"/>
  <path d="M600,25 C800,45 1000,50 1200,35 L1200,60 L600,60Z" fill="#3b9ad8"/>
</svg>
<h2 class="abs heading services-title">Our Services</h2>

<div class="card-photo" style="left:47px;background:linear-gradient(160deg,#2f4a37 0%,#1d3d66 45%,#3aa6d9 80%)" role="img" aria-label="Technician cleaning a pool filter at the water's edge"></div>
<h3 class="card-title" style="left:47px">Pool Services</h3>
<p class="card-text" style="left:47px">When you invested in your pool, you knew it was a long-term investment in both money and time. At home, it’s an oasis.</p>
<div class="btn" style="left:156px;top:2427px;width:132px;height:32px">Learn More</div>

<div class="card-photo" style="left:424px;background:linear-gradient(180deg,#6d6c66 0%,#8c8a82 35%,#48b6e4 60%,#b0765c 100%)" role="img" aria-label="Commercial resort pool with lounge chairs"></div>
<h3 class="card-title" style="left:424px">Commercial Pool</h3>
<p class="card-text" style="left:424px">As a commercial property owner or manager, doing your job well requires you to be mindful of all the details.</p>
<div class="btn" style="left:533px;top:2427px;width:132px;height:32px">Learn More</div>

<div class="card-photo" style="left:800px;background:linear-gradient(180deg,#4c7a3a 0%,#8aa35a 45%,#2fbfe3 75%,#1fa3d1 100%)" role="img" aria-label="Residential backyard pool with tropical garden"></div>
<h3 class="card-title" style="left:800px">Residential Pool</h3>
<p class="card-text" style="left:800px">Here in Southern Nevada, you know it can get really, really hot. That’s why you your pool at off and relax with family and friends.</p>
<div class="btn" style="left:909px;top:2427px;width:132px;height:32px">Learn More</div>

<!-- contact -->
<div class="abs contact-bg"></div>
<svg class="abs" style="left:0;top:2520px" width="1200" height="110" viewBox="0 0 1200 110">
  <path d="M0,0 L1200,0 L1200,40 C1000,20 820,40 600,70 C380,100 150,100 0,80Z" fill="#3b9ad8"/>
  <path d="M620,70 C800,30 1000,10 1200,38 L1200,45 C1000,30 820,60 620,70Z" fill="#1c4a7f"/>
  <path d="M640,75 C820,40 1000,25 1200,45 L1200,55 C1000,45 820,70 640,75Z" fill="#1c4a7f"/>
</svg>
<div class="photo abs contact-photo" role="img" aria-label="Smiling woman in sunglasses leaning on a pool float"></div>
<h2 class="abs heading contact-title">Get In Touch</h2>
<div class="field" style="left:191px;top:2758px;width:403px;height:50px">First Name*</div>
<div class="field" style="left:608px;top:2758px;width:402px;height:50px">Last Name*</div>
<div class="field" style="left:191px;top:2822px;width:403px;height:52px">E-mail*</div>
<div class="field" style="left:608px;top:2822px;width:402px;height:52px">Phone*</div>
<div class="field" style="left:191px;top:2888px;width:819px;height:138px;border-radius:14px">Message*</div>
<div class="btn" style="left:519px;top:3057px;width:162px;height:32px">Send</div>

<!-- cta -->
<div class="photo cta-photo" role="img" aria-label="Technician vacuuming an outdoor pool"></div>
<svg class="abs" style="left:0;top:3150px" width="1200" height="70" viewBox="0 0 1200 70">
  <path d="M0,0 L1200,0 L1200,45 C950,25 800,20 600,10 C400,0 200,40 0,45Z" fill="#f4f4f2"/>
</svg>
<div class="abs cta-box"></div>
<h2 class="abs cta-title">Coral Bay<br>Pools</h2>
<div class="btn" style="left:523px;top:3474px;width:155px;height:32px">Free Estimate</div>

<!-- footer -->
<div class="abs footer-bg"></div>
<svg class="abs" style="left:0;top:3620px" width="1200" height="80" viewBox="0 0 1200 80">
  <path d="M0,30 C200,60 450,70 700,50 C900,35 1050,20 1200,10 L1200,80 L0,80Z" fill="#3b9ad8"/>
  <path d="M0,45 C250,75 500,80 750,60 C950,45 1080,30 1200,22 L1200,80 L0,80Z" fill="#1e2633"/>
</svg>
<div class="brand" style="left:495px;top:3765px;color:#fff"><span class="dot"></span>Coral Bay Pools</div>
<nav class="footer-nav">
  <a style="left:303px">Home</a>
  <a style="left:410px">About Us</a>
  <a style="left:536px">Our Services</a>
  <a style="left:684px">Free Estimate</a>
  <a style="left:841px">Contact</a>
</nav>
<div class="abs footer-rule" style="top:3926px"></div>
<div class="contact-item" style="left:221px">
  <span class="contact-icon"><svg width="14" height="14" viewBox="0 0 24 24"><path d="M6.6 10.8a15 15 0 0 0 6.6 6.6l2.2-2.2a1 1 0 0 1 1-.25 11.4 11.4 0 0 0 3.6.6 1 1 0 0 1 1 1V20a1 1 0 0 1-1 1A17 17 0 0 1 3 4a1 1 0 0 1 1-1h3.5a1 1 0 0 1 1 1c0 1.25.2 2.45.6 3.6a1 1 0 0 1-.25 1z" fill="#fff"/></svg></span>(702) 555-0148
</div>
<div class="contact-item" style="left:391px">
  <span class="contact-icon"><svg width="14" height="14" viewBox="0 0 24 24"><rect x="3" y="5" width="18" height="14" rx="2" fill="#fff"/><path d="M3 7l9 6 9-6" stroke="#f9a11b" stroke-width="1.8" fill="none"/></svg></span>poolsolutions@coralbaypoolslv.com
</div>
<span class="social" style="left:877px"></span>
<span class="social" style="left:920px"></span>
<span class="social" style="left:962px"></span>
<div class="abs footer-rule" style="top:3999px"></div>
<p class="abs copyright">©2026 Coral Bay Pools - All rights reserved.</p>

</body>
</html>
```